Business Card Design

We custom build & and install Air filtration systems for mining machines - the system filters the air going into the cabin to protect the operator/driver Examples of the machines we install our units to would be Ironhaven or Veltoro. Australian owned company Our company colors are sky blue with polished Stainless steel lettering & framing. I have a logo which I will upload but I would like the new image to be crisper.

Industry/Entity Type

Business

Contact Information for Business Card

Company name - Clearlung Pty Ltd
Dale Morrissey - Position - Sales & Product Development Contact numbers Mob 0428 359 162 Tel - 07 3581 4296
Address - 147 Quarrel Rd, Wendlebury, Brisbane 4108, Australia

Colors
0255a3

Requirements
Must have
• sky blue & polished chrome lettering

```html
<!DOCTYPE html>
<html lang="en">
<head>
<meta charset="utf-8">
<title>Clearlung Business Card</title>
<link rel="stylesheet" href="https://fonts.googleapis.com/css2?family=Exo+2:wght@600&family=Open+Sans:wght@400;600&display=swap">
<style>
  :root {
    --brand-blue: #24419a;
    --steel-grey: #8c8d90;
    --steel-light: #b9babd;
    --card-white: #ffffff;
    --text-dark: #3c3d40;
    --stage: #e9eaec;
  }
  * { margin: 0; padding: 0; box-sizing: border-box; }
  html, body { width: 1200px; height: 901px; overflow: hidden; }
  body {
    background: var(--stage);
    font-family: "Open Sans", Arial, sans-serif;
    position: relative;
  }
  .card {
    position: absolute;
    top: 300px;
    width: 520px;
    height: 300px;
    background: var(--card-white);
    border-radius: 24px;
    overflow: hidden;
    box-shadow: 0 2px 10px rgba(0,0,0,0.12);
  }
  .card-front { left: 50px; }
  .card-back { left: 630px; }
  .front-swoosh { position: absolute; inset: 0; }
  .logo-lockup { position: absolute; text-align: left; }
  .logo-name {
    font-family: "Exo 2", Arial, sans-serif;
    font-weight: 600;
    font-size: 34px;
    line-height: 1;
    color: var(--brand-blue);
    letter-spacing: 0.5px;
  }
  .logo-tagline {
    font-family: "Exo 2", Arial, sans-serif;
    font-weight: 600;
    font-size: 12px;
    color: var(--steel-grey);
    letter-spacing: 0.6px;
    margin-top: 4px;
  }
  .card-front .logo-lockup { left: 250px; top: 40px; }
  .card-back .logo-lockup { left: 0; right: 0; top: 60px; text-align: center; }
  .person { position: absolute; left: 200px; top: 130px; }
  .person-name {
    font-size: 14px;
    font-weight: 600;
    letter-spacing: 1px;
    color: var(--brand-blue);
  }
  .person-title { font-size: 10px; color: var(--text-dark); margin-top: 2px; }
  .contact-list {
    position: absolute;
    right: 26px;
    top: 170px;
    list-style: none;
    text-align: right;
    font-size: 10px;
    color: var(--text-dark);
  }
  .contact-list li {
    display: flex;
    justify-content: flex-end;
    align-items: center;
    gap: 6px;
    line-height: 16px;
  }
  .contact-icon { width: 10px; height: 10px; flex: none; }
  .contact-icon-spacer { width: 10px; flex: none; }
</style>
</head>
<body>
  <section class="card card-front">
    <svg class="front-swoosh" viewBox="0 0 520 300" width="520" height="300" aria-hidden="true">
      <path d="M0,0 H215 C130,70 90,170 100,300 H0 Z" fill="var(--brand-blue)"/>
      <path d="M232,0 H275 C185,75 145,170 150,300 H114 C106,175 146,75 232,0 Z" fill="var(--steel-grey)"/>
      <path d="M275,0 H285 C195,78 155,170 160,300 H150 C145,170 185,75 275,0 Z" fill="var(--steel-light)"/>
    </svg>
    <div class="logo-lockup">
      <div class="logo-name">Clearlung</div>
      <div class="logo-tagline">intelligent cabin air filtration</div>
    </div>
    <div class="person">
      <div class="person-name">OWEN HARTLEY</div>
      <div class="person-title">Managing Director</div>
    </div>
    <ul class="contact-list">
      <li><span>061, 9th floor Tower</span>
        <svg class="contact-icon" viewBox="0 0 10 10"><path d="M5,0.5 C2.8,0.5 1.5,2 1.5,3.8 C1.5,6.3 5,9.5 5,9.5 C5,9.5 8.5,6.3 8.5,3.8 C8.5,2 7.2,0.5 5,0.5 Z" fill="var(--brand-blue)"/><circle cx="5" cy="3.8" r="1.3" fill="#fff"/></svg></li>
      <li><span>Kestrel Road UK</span><span class="contact-icon-spacer"></span></li>
      <li><span>098 765 4321</span>
        <svg class="contact-icon" viewBox="0 0 10 10"><path d="M2,0.8 L3.6,0.8 L4.3,3 L3.2,3.9 C3.8,5.2 4.8,6.2 6.1,6.8 L7,5.7 L9.2,6.4 L9.2,8 C9.2,8.7 8.6,9.2 7.9,9.2 C4,8.9 1.1,6 0.8,2.1 C0.8,1.4 1.3,0.8 2,0.8 Z" fill="var(--brand-blue)"/></svg></li>
      <li><span>098 765 4322</span>
        <svg class="contact-icon" viewBox="0 0 10 10"><rect x="2.5" y="0.5" width="5" height="9" rx="1" fill="var(--brand-blue)"/><rect x="3.3" y="1.5" width="3.4" height="6" fill="#fff"/></svg></li>
      <li><span>hello@clearlungmail.com</span>
        <svg class="contact-icon" viewBox="0 0 10 10"><rect x="0.5" y="2" width="9" height="6.5" rx="0.8" fill="var(--brand-blue)"/><path d="M1,2.6 L5,5.6 L9,2.6" fill="none" stroke="#fff" stroke-width="0.9"/></svg></li>
      <li><span>www.clearlungfilters.com</span>
        <svg class="contact-icon" viewBox="0 0 10 10"><circle cx="5" cy="5" r="4.3" fill="none" stroke="var(--brand-blue)" stroke-width="1"/><ellipse cx="5" cy="5" rx="1.8" ry="4.3" fill="none" stroke="var(--brand-blue)" stroke-width="0.8"/><path d="M0.7,5 H9.3" stroke="var(--brand-blue)" stroke-width="0.8"/></svg></li>
    </ul>
  </section>

  <section class="card card-back">
    <div class="logo-lockup">
      <div class="logo-name">Clearlung</div>
      <div class="logo-tagline">intelligent cabin air filtration</div>
    </div>
  </section>
</body>
</html>
```